Timber Crest Construction Needs business card

Hey we are in need of business card designs. I have upload our logo as a guideline, but free feel to run with it or come up with something unique.
Pls have fun with it and be creative. the name says it all!
i will give some directions after i see a few entries..
Updates
Logo source file has been uploaded..
Hey because of the logo is so colourful already.
Can we have a few submissions with less colour.
Also we are looking for clever/hidden/descriptive business card.

```html
<!DOCTYPE html>
<html lang="en">
<head>
<meta charset="utf-8">
<title>Timber Crest Construction – Business Card</title>
<link href="https://fonts.googleapis.com/css2?family=Didact+Gothic&display=swap" rel="stylesheet">
<style>
  :root {
    --backdrop: #1f7f00;
    --card-dark: #000000;
    --card-light: #ffffff;
    --brand-grey: #808285;
    --ink: #231f20;
    --accent-red: #ed1c24;
    --pattern-a: #2a2a2c;
    --pattern-b: #3a3a3d;
  }
  * { margin: 0; padding: 0; box-sizing: border-box; }
  html, body { width: 1200px; height: 1200px; overflow: hidden; }
  body {
    background: var(--backdrop);
    position: relative;
    font-family: "Didact Gothic", "Century Gothic", sans-serif;
  }
  .card {
    position: absolute;
    left: 212px;
    width: 800px;
    height: 445px;
    overflow: hidden;
  }
  .card--front { top: 130px; background: var(--card-dark); }
  .card--back { top: 641px; background: var(--card-light); }

  .front-pattern {
    position: absolute;
    left: 8px; top: 0;
    width: 320px; height: 445px;
    background: linear-gradient(160deg, var(--pattern-b), var(--pattern-a));
  }

  .wordmark {
    position: absolute;
    display: flex;
    align-items: center;
    gap: 14px;
    color: var(--brand-grey);
    font-weight: 400;
    text-transform: uppercase;
    line-height: 1.05;
  }
  .wordmark__square {
    width: 30px; height: 30px;
    background: var(--brand-grey);
    flex: none;
  }
  .wordmark__name { font-size: 34px; letter-spacing: 1px; }
  .wordmark__name span { display: block; font-size: 34px; }
  .card--front .wordmark { left: 366px; top: 170px; }
  .card--back .wordmark { left: 86px; top: 170px; }

  .contact {
    position: absolute;
    left: 443px; top: 124px;
    color: var(--ink);
    font-size: 14px;
    letter-spacing: 2.6px;
  }
  .contact__name { font-weight: 700; font-size: 15px; letter-spacing: 3.4px; }
  .contact__role { color: var(--accent-red); font-size: 14px; letter-spacing: 2.4px; }
  .contact__sep { margin: 0 10px; }
  .contact__address { margin-top: 30px; line-height: 21px; text-transform: uppercase; }
  .contact__list { list-style: none; margin-top: 20px; }
  .contact__list li { display: flex; align-items: center; height: 25px; }
  .contact__icon { width: 16px; height: 14px; margin-right: 20px; }
  .contact__icon svg { display: block; width: 16px; height: 14px; fill: none; stroke: var(--accent-red); stroke-width: 1.6; }
</style>
</head>
<body>

<section class="card card--front">
  <div class="front-pattern" role="img" aria-label="Decorative pattern of coloured building blocks"></div>
  <div class="wordmark">
    <div class="wordmark__square"></div>
    <div class="wordmark__name">Timber Crest<span>Construction</span></div>
  </div>
</section>

<section class="card card--back">
  <div class="wordmark">
    <div class="wordmark__square"></div>
    <div class="wordmark__name">Timber Crest<span>Construction</span></div>
  </div>

  <div class="contact">
    <p><span class="contact__name">MARCO DELANE</span><span class="contact__sep">-</span><span class="contact__role">DIRECTOR</span></p>
    <p class="contact__address">Shop 4, 212-216 Harbour<br>Road Westfield North</p>
    <ul class="contact__list">
      <li><span class="contact__icon"><svg viewBox="0 0 16 14"><path d="M2 5 Q8 0 14 5 L12 6 L10 4 L6 4 L4 6 Z"/><rect x="3" y="8" width="10" height="5"/></svg></span>9731 2054</li>
      <li><span class="contact__icon"><svg viewBox="0 0 16 14"><rect x="4" y="1" width="8" height="4"/><rect x="1.5" y="5" width="13" height="5"/><rect x="4" y="9" width="8" height="4"/></svg></span>9731 2087</li>
      <li><span class="contact__icon"><svg viewBox="0 0 16 14"><rect x="1" y="2" width="14" height="10"/><path d="M1 2 L8 8 L15 2"/></svg></span>marco@timbercrestbuild.com</li>
      <li><span class="contact__icon"><svg viewBox="0 0 16 14"><circle cx="7" cy="7" r="6"/><path d="M1 7 H13 M7 1 V13 M3 3 Q7 6 11 3 M3 11 Q7 8 11 11"/></svg></span>www.timbercrestbuild.com</li>
    </ul>
  </div>
</section>

</body>
</html>
```